KRV Business Card

Looking for a business card for my restaurant group I own. Four different concepts:

Copperfield Alehouse
Bristow Alehouse
Tanager's Stone Hearth Kitchen
Pellston Patty Company

Card doesn't need to include all the logos.

```html
<!DOCTYPE html>
<html lang="en">
<head>
<meta charset="utf-8">
<title>KRV Business Card</title>
<link rel="stylesheet" href="https://fonts.googleapis.com/css2?family=Lato:wght@400;700&display=swap">
<style>
  :root {
    --page: #ecebe8;
    --gold: #d3af6a;
    --gold-deep: #c9a25a;
    --slate: #6b6c70;
    --disc: #f3f2ef;
    --ink-light: #ffffff;
    --rule: rgba(255,255,255,0.7);
  }
  * { margin: 0; padding: 0; box-sizing: border-box; }
  html, body { width: 1200px; height: 900px; overflow: hidden; background: var(--page); }
  body { position: relative; font-family: "Lato", sans-serif; }

  .business-card {
    position: absolute; left: 112px; top: 146px;
    width: 975px; height: 608px; overflow: hidden;
    background: var(--gold);
    box-shadow: 0 14px 40px rgba(0,0,0,0.18);
  }
  .side-band {
    position: absolute; left: 660px; top: 0; width: 315px; height: 100%;
    background: var(--slate);
  }
  .brand-disc {
    position: absolute; left: 401px; top: 35px;
    width: 524px; height: 524px; border-radius: 50%;
    background: var(--disc);
    display: flex; flex-direction: column; align-items: center; justify-content: center;
  }
  .brand-name {
    color: var(--gold-deep); font-weight: 700; text-align: center;
    letter-spacing: 0.12em; line-height: 1.1;
  }
  .brand-name .brand-initials { display: block; font-size: 90px; letter-spacing: 0.18em; margin-left: 0.18em; }
  .brand-name .brand-rest { display: block; font-size: 28px; margin-top: 14px; }

  .contact-block { position: absolute; left: 56px; top: 62px; color: var(--ink-light); }
  .holder-name { font-size: 33px; font-weight: 400; letter-spacing: 0.02em; line-height: 1; }
  .holder-role { font-size: 26px; margin-top: 8px; line-height: 1; }
  .contact-list { list-style: none; margin-top: 30px; }
  .contact-list li { display: flex; align-items: center; gap: 9px; font-size: 25px; height: 36px; }
  .contact-list svg { width: 18px; height: 18px; flex: none; }
  .address { font-size: 25px; line-height: 36px; margin-top: 12px; }

  .divider { position: absolute; left: 62px; top: 390px; width: 294px; height: 1.5px; background: var(--rule); }

  .concept-list {
    position: absolute; left: 60px; top: 427px; list-style: none;
    color: var(--ink-light); font-weight: 700; font-size: 21px; text-transform: uppercase;
  }
  .concept-list li { display: flex; align-items: center; gap: 10px; height: 31px; white-space: nowrap; }
  .concept-list li::before {
    content: ""; width: 13px; height: 13px; border-radius: 50%; background: var(--ink-light); flex: none;
  }
</style>
</head>
<body>
  <section class="business-card">
    <div class="side-band"></div>

    <div class="brand-disc">
      <p class="brand-name"><span class="brand-initials">KRV</span><span class="brand-rest">HOSPITALITY GROUP</span></p>
    </div>

    <div class="contact-block">
      <h1 class="holder-name">DANIEL HARPER</h1>
      <p class="holder-role">Managing Director</p>
      <ul class="contact-list">
        <li>
          <svg viewBox="0 0 24 24" aria-hidden="true"><path fill="#fff" d="M6.6 10.8a15 15 0 0 0 6.6 6.6l2.2-2.2c.3-.3.7-.4 1-.2 1.1.4 2.3.6 3.6.6.6 0 1 .4 1 1V20c0 .6-.4 1-1 1A17 17 0 0 1 3 4c0-.6.4-1 1-1h3.5c.6 0 1 .4 1 1 0 1.2.2 2.4.6 3.6.1.3 0 .7-.2 1z"/></svg>
          044-987 654 321
        </li>
        <li>
          <svg viewBox="0 0 24 24" aria-hidden="true"><rect x="2" y="5" width="20" height="14" fill="#fff"/><path d="M2 5l10 8 10-8" fill="none" stroke="#d3af6a" stroke-width="2"/></svg>
          hello@krvgroup.com
        </li>
        <li>
          <svg viewBox="0 0 24 24" aria-hidden="true"><circle cx="12" cy="12" r="10" fill="#fff"/><path d="M2 12h20M12 2c3 3 3 17 0 20M12 2c-3 3-3 17 0 20" fill="none" stroke="#d3af6a" stroke-width="1.5"/></svg>
          www.krvgroup.com
        </li>
      </ul>
      <p class="address">421, Address line here,<br>45452,Country Name</p>
    </div>

    <div class="divider"></div>

    <ul class="concept-list">
      <li>Copperfield Alehouse</li>
      <li>Bristow Alehouse</li>
      <li>Tanager's Stone Hearth Kitchen</li>
      <li>Pellston Patty Company</li>
    </ul>
  </section>
</body>
</html>
```